Business card design for modern PanoWalk agency

Hello,

I need a business card design for my company Kites7Market.
We mainly offer Zorvex PanoWalk Tours (360° Photography) and it should be a business card with following details:

Name: Tobias Wendler
Number: +49 176 58 20 917
Mail: tobias@kites7market.com
website: kites7market.com

Main colour that we use is the red of the logo.
It´s also important to integrate the "Zorvex Verified logo" as the person on this business card is a Zorvex verified photographer.

And if possible we would also like to integrate something like send us a sms or quipchat and we call you back. As the number is german but we sell now in Vienna, Austria.

We offer a good price but very high photography quality, as we are mostly students - that´s our concept.

Maybe an idea is to integrate something 360° on the back-side of the card, for example the photo attached (just an idea) or some great design.
See flyer (attached) and kites7market.com for inspiration, maybe use of the photo of me (attached) in a circle or something

I´m very excited for your designs and thanks a lot in advance!! :)

Target Market(s)

Shops, hotels, shopping centers, etc. in Vienna, Austria

Industry/Entity Type

Business

Contact Information for Business Card

double-sided, use red of the logo, 360° zorvex pano walk certified photographer

Font styles to use
Serif
Sans Serif

Colors
ec1f27

Requirements
Nice to have
• maybe some 360° design on back-side
• maybe include photo of me in a circle or something or sketched in red colour

```html
<!DOCTYPE html>
<html lang="en">
<head>
<meta charset="utf-8">
<title>Kites7Market – Business Card</title>
<link rel="stylesheet" href="https://fonts.googleapis.com/css2?family=Open+Sans:wght@400;600;700&display=swap">
<style>
  :root {
    --stage: #1f1f1f;
    --brand-red: #e4132b;
    --brand-grey: #a6a8ab;
    --ink: #222222;
    --card-white: #ffffff;
    --band-grey: #e3e3e4;
    --badge-text: #5f6368;
    --badge-dot: #1e9e4a;
  }
  * { margin: 0; padding: 0; box-sizing: border-box; }
  html, body { width: 1200px; height: 900px; overflow: hidden; }
  body {
    background: radial-gradient(ellipse at 50% 40%, #2b2b2b 0%, var(--stage) 75%);
    font-family: "Open Sans", Arial, sans-serif;
    position: relative;
  }
  .card {
    position: absolute;
    top: 306px;
    width: 439px;
    height: 271px;
    border-radius: 10px;
    overflow: hidden;
    box-shadow: 0 4px 14px rgba(0,0,0,0.45);
  }
  .card--front { left: 149px; background: var(--card-white); }
  .card--back  { left: 609px; background: var(--band-grey); }

  /* front */
  .name-tab { position: absolute; left: 0; top: 35px; }
  .holder-name {
    position: absolute; left: 32px; top: 40px;
    font-size: 14px; font-weight: 700; color: var(--brand-red);
    letter-spacing: 0.2px;
  }
  .brand-lockup {
    position: absolute; right: 25px; top: 67px;
    display: flex; align-items: center; gap: 10px;
  }
  .brand-lockup__square { width: 62px; height: 62px; background: var(--brand-red); }
  .brand-lockup__name {
    font-weight: 700; font-size: 30px; line-height: 30px;
    color: var(--brand-grey); text-transform: uppercase; text-align: left;
    letter-spacing: -0.5px;
  }
  .contact-list {
    position: absolute; left: 28px; top: 182px;
    list-style: none; font-size: 12px; color: var(--ink); line-height: 15.5px;
  }
  .contact-list li { display: flex; align-items: center; gap: 6px; }
  .contact-list svg { width: 9px; height: 9px; fill: var(--brand-red); flex: none; }
  .callback-note {
    position: absolute; right: 25px; top: 185px;
    text-align: right; font-size: 13px; font-weight: 600;
    color: var(--brand-red); line-height: 18px;
  }
  .footer-band { position: absolute; left: 0; bottom: 0; }

  /* back */
  .back-panel {
    position: absolute; left: 0; top: 0; width: 100%; height: 212px;
    background: linear-gradient(180deg, #e8172f 0%, #df1129 100%);
  }
  .brand-lockup--light {
    right: auto; left: 50%; top: 104px; transform: translateX(-50%);
  }
  .brand-lockup--light .brand-lockup__square { background: #ffffff; }
  .brand-lockup--light .brand-lockup__name { color: #ffffff; }
  .verified-mark {
    position: absolute; left: 0; right: 0; top: 223px;
    display: flex; justify-content: center; align-items: center; gap: 7px;
  }
  .verified-mark__dot { width: 11px; height: 11px; border-radius: 50%; background: var(--badge-dot); }
  .verified-mark__text {
    font-size: 14px; font-weight: 400; color: var(--badge-text); line-height: 16px; text-align: center;
  }
</style>
</head>
<body>

<section class="card card--front" aria-label="Business card front">
  <svg class="name-tab" width="26" height="30" viewBox="0 0 26 30" aria-hidden="true">
    <polygon points="0,0 5,0 11,30 0,30" fill="#e4132b"/>
    <polygon points="8,0 24,0 24,30 14,30" fill="#a6a8ab"/>
  </svg>
  <h1 class="holder-name">TOBIAS WENDLER</h1>

  <div class="brand-lockup">
    <div class="brand-lockup__square"></div>
    <div class="brand-lockup__name">Kites7<br>Market</div>
  </div>

  <ul class="contact-list">
    <li>
      <svg viewBox="0 0 10 10" aria-hidden="true"><path d="M2 0.5 L3.6 2.6 L2.8 3.6 Q3.8 5.8 6.2 7 L7.2 6.2 L9.5 7.8 L8.4 9.5 Q3.5 9 0.6 2 Z"/></svg>
      +49 176 58 20 917
    </li>
    <li>
      <svg viewBox="0 0 10 10" aria-hidden="true"><path d="M0 2 H10 V8.5 H0 Z M0.8 2.6 L5 5.6 L9.2 2.6 V3.4 L5 6.4 L0.8 3.4 Z" fill-rule="evenodd"/></svg>
      tobias@kites7market.com
    </li>
    <li>
      <svg viewBox="0 0 10 10" aria-hidden="true"><circle cx="5" cy="5" r="4.6"/></svg>
      www.kites7market.com
    </li>
  </ul>

  <p class="callback-note">Send us a sms or quipchat<br>and we call you back</p>

  <svg class="footer-band" width="439" height="20" viewBox="0 0 439 20" aria-hidden="true">
    <polygon points="0,6 218,6 210,20 0,20" fill="#e4132b"/>
    <polygon points="222,0 439,0 439,20 208,20" fill="#a6a8ab"/>
  </svg>
</section>

<section class="card card--back" aria-label="Business card back">
  <div class="back-panel" role="img" aria-label="Red field with a repeating small brand-square pattern"></div>
  <div class="brand-lockup brand-lockup--light">
    <div class="brand-lockup__square"></div>
    <div class="brand-lockup__name">Kites7<br>Market</div>
  </div>
  <div class="verified-mark">
    <div class="verified-mark__dot"></div>
    <p class="verified-mark__text">Zorvex PanoWalk<br>verified</p>
  </div>
</section>

</body>
</html>
```